Best local air conditioning and heating contractor

We need a website design for a new company in Tampa Bay called the Coastal Breeze Cooling Company. We provide superior services for residential and commercial properties as well as maintenance and installing HVAC systems. We also want to sell equipment, parts and filter on the website as well. We want it easy to use for customers. Rich with content and keywords for our area.

Target Market(s)

homeowners in Tampa Bay

Industry/Entity Type

HVAC air conditioning and heating

Coding

Coded - Design and coding required

Number of Pages Required

5+ page

Font styles to use
Sans Serif

Requirements
Nice to have
• would like the colors to be same as logo

```html
<!DOCTYPE html>
<html lang="en">
<head>
<meta charset="UTF-8">
<title>Coastal Breeze Cooling Company</title>
<link href="https://fonts.googleapis.com/css2?family=Krona+One&family=Poppins:ital,wght@0,400;0,500;0,600;0,700;1,400&display=swap" rel="stylesheet">
<style>
:root{
  --navy:#1f3a7a;
  --navy-dark:#13265a;
  --navy-deep:#0e1d45;
  --red:#d9242b;
  --red-dark:#b81c22;
  --ink:#1b1b1b;
  --text:#4a4f5c;
  --light:#eef2f8;
  --white:#fff;
}
*{margin:0;padding:0;box-sizing:border-box}
html,body{width:1200px;height:5329px;overflow:hidden}
body{font-family:'Poppins',sans-serif;color:var(--text);background:#fff;position:relative}
.abs{position:absolute}
.display{font-family:'Krona One',sans-serif;text-transform:uppercase;letter-spacing:1px;line-height:1.05;color:var(--ink)}
.display .accent{color:var(--red);position:relative}
.display .accent.line::after{content:"";position:absolute;left:25%;right:25%;bottom:-10px;height:3px;background:var(--red)}
.btn{position:absolute;display:flex;align-items:center;justify-content:center;background:var(--red);color:#fff;font-weight:600;font-size:13px;text-transform:uppercase;letter-spacing:.3px}
.fill{position:absolute}
.call{position:absolute;display:flex;align-items:center;gap:12px}
.call .ico{width:40px;height:40px;border-radius:50%;background:var(--navy);display:flex;align-items:center;justify-content:center}
.call small{display:block;font-size:11px;color:var(--navy)}
.call strong{display:block;font-size:19px;font-weight:500;color:var(--navy);line-height:1}

/* top bar */
.topbar{top:0;left:0;width:1200px;height:26px;background:var(--navy-deep);color:#fff;font-size:10.5px}
.topbar span{position:absolute;top:6px}
.topbar .stars{color:#f5b400}
.topbar .soc{position:absolute;top:6px;width:14px;height:14px;border:1px solid rgba(255,255,255,.6);border-radius:2px}

/* header */
.header{top:26px;left:0;width:1200px;height:78px;background:#fff}
.brand{position:absolute;display:flex;align-items:center;gap:8px;font-weight:700;color:var(--navy);text-transform:uppercase;line-height:1.1}
.brand i{display:block;background:var(--red);border-radius:50%}
.nav a{position:absolute;top:32px;font-size:13px;font-weight:500;color:var(--ink);text-decoration:none;text-transform:uppercase}
.callbadge{position:absolute;left:906px;top:4px;width:294px;height:70px;background:var(--red);border-radius:35px 0 0 35px;color:#fff}
.callbadge .ring{position:absolute;left:-28px;top:9px;width:52px;height:52px;border-radius:50%;background:var(--navy);border:4px solid #fff;display:flex;align-items:center;justify-content:center}
.callbadge small{position:absolute;left:30px;top:10px;font-size:14px}
.callbadge strong{position:absolute;left:30px;top:30px;font-size:27px;font-weight:600;letter-spacing:.5px}

/* hero */
.hero{top:104px;left:0;width:1200px;height:624px;background:linear-gradient(110deg,#5a3a4a 0%,#8a5f6e 35%,#c9a9b6 65%,#9b8aa6 100%)}
.hero .shade{position:absolute;inset:0;background:linear-gradient(90deg,rgba(60,30,70,.55),rgba(60,30,70,0) 60%)}
.hero-title{left:100px;top:252px;font-size:28px;color:#fff;letter-spacing:2px}

/* schedule */
.schedule{top:728px;left:0;width:1200px;height:182px;background:linear-gradient(180deg,var(--navy-dark),var(--navy))}
.schedule h2{left:100px;top:46px;font-size:22px;color:#fff;letter-spacing:2px}
.field{position:absolute;background:#fff;font-size:12px;color:#555;padding:0 12px;display:flex;align-items:center}
.schedule .field{top:93px;height:36px}
.van{background:linear-gradient(100deg,#c8202a,#e44a3a 45%,#1a2c66 80%,#2d2d2d)}

/* about */
.about-frame{left:90px;top:977px;width:468px;height:450px;border:6px solid var(--red);border-right:none;border-bottom:none}
.about-p{left:645px;width:460px;font-size:12.5px;line-height:26px;color:var(--text)}

/* services */
.services{top:1562px;left:0;width:1200px;height:646px;background:var(--light)}
.card{position:absolute;top:151px;width:318px;height:414px;background:#fff;box-shadow:0 4px 14px rgba(20,40,90,.08);text-align:center}
.card .photo{position:absolute;left:0;top:0;width:318px;height:202px}
.card .badge{position:absolute;left:129px;top:172px;width:60px;height:60px;border-radius:50%;background:var(--navy);border:4px solid #fff;display:flex;align-items:center;justify-content:center}
.card h3{position:absolute;top:250px;width:100%;font-size:21px;font-weight:500;color:var(--ink)}
.card p{position:absolute;top:290px;left:18px;right:18px;font-size:12.5px;line-height:26px}
.card a{position:absolute;top:374px;left:0;right:0;font-size:13px;font-weight:600;color:var(--red);text-decoration:underline}

/* emergency */
.emergency-p{left:100px;top:2365px;width:460px;font-size:12.6px;line-height:25.6px}

/* why */
.why{top:2746px;left:0;width:1200px;height:596px;background:linear-gradient(180deg,#f4f6fb,#e9edf5)}
.feat{position:absolute;display:flex;align-items:center;gap:14px;font-size:15px;font-weight:600;color:var(--ink);text-transform:uppercase;line-height:1.15}
.feat .dot{width:62px;height:62px;border-radius:50%;background:var(--red);display:flex;align-items:center;justify-content:center;flex:none;box-shadow:0 0 0 5px rgba(217,36,43,.15)}
.feat.left{justify-content:flex-end;text-align:right}

/* testimonials */
.reviews{top:3342px;left:0;width:1200px;height:403px;background:var(--navy)}
.review{position:absolute;top:76px;width:292px;height:207px;background:#fff;border-bottom:5px solid var(--red);padding:18px 20px}
.review p{font-size:11.5px;font-style:italic;line-height:21px;color:#333}
.review .who{position:absolute;left:22px;bottom:18px;display:flex;align-items:center;gap:10px}
.review .av{width:34px;height:34px;border-radius:50%;background:linear-gradient(#c7b8a8,#8f7d6b)}
.review b{display:block;font-size:13px;font-weight:600;color:var(--navy)}
.review .st{color:#f5b400;font-size:11px;letter-spacing:1px}
.arrow{position:absolute;width:30px;height:30px;border-radius:50%;border:2px solid #fff;display:flex;align-items:center;justify-content:center}

/* works */
.tile{position:absolute;height:238px}

/* contact */
.contact{top:4444px;left:0;width:1200px;height:522px;background:linear-gradient(100deg,#3b4150,#6b6f78 40%,#4a4f5a 70%,#2f3440)}
.contact .field{height:42px;font-size:14px;color:#666}

/* footer */
.footer{top:4966px;left:0;width:1200px;height:363px;background:var(--navy-dark);border-top:6px solid var(--red);color:#fff}
.footer h4{position:absolute;top:62px;font-size:15px;font-weight:500}
.footer ul{position:absolute;top:100px;list-style:none;font-size:12px;line-height:31px;color:#dfe5f3}
.footer .s{position:absolute;top:185px;width:36px;height:36px;border-radius:50%;background:#fff}
.footer .rule{position:absolute;left:100px;right:100px;top:293px;height:1px;background:rgba(255,255,255,.25)}
.footer .copy{position:absolute;top:305px;width:100%;text-align:center;font-size:12.5px;color:#e5e9f3}
</style>
</head>
<body>

<!-- top bar -->
<div class="abs topbar">
  <span style="left:100px"><b class="stars">★★★★★</b> 4.8 STAR SERVICES (20REVIEWS)</span>
  <span style="left:375px">● Mon to Fri 9:00 am to 6:00 pm</span>
  <span style="left:800px">● Serving The Tampa Bay Area</span>
  <i class="soc" style="left:988px"></i><i class="soc" style="left:1018px"></i><i class="soc" style="left:1048px"></i><i class="soc" style="left:1078px"></i>
</div>

<!-- header -->
<header class="abs header">
  <div class="brand" style="left:100px;top:18px;font-size:13px"><i style="width:16px;height:16px"></i><span>Coastal Breeze<br>Cooling Company</span></div>
  <nav class="nav">
    <a style="left:375px">About Us</a><a style="left:478px">Services</a><a style="left:578px">HVAC</a><a style="left:648px">Resources</a><a style="left:763px">Contact</a>
  </nav>
  <div class="callbadge">
    <div class="ring"><svg width="20" height="20" viewBox="0 0 24 24"><path fill="#fff" d="M6.6 10.8a15.1 15.1 0 006.6 6.6l2.2-2.2c.3-.3.7-.4 1-.2 1.1.4 2.3.6 3.6.6.6 0 1 .4 1 1V20c0 .6-.4 1-1 1A17 17 0 013 4c0-.6.4-1 1-1h3.5c.6 0 1 .4 1 1 0 1.3.2 2.5.6 3.6.1.3 0 .7-.2 1z"/></svg></div>
    <small>Call Today for Service</small>
    <strong>727 - 555 - 0142</strong>
  </div>
</header>

<!-- hero -->
<section class="abs hero" role="img" aria-label="Close-up photo of HVAC pressure gauges on an outdoor condenser unit">
  <div class="shade"></div>
</section>
<div class="fill" style="left:683px;top:112px;width:290px;height:616px;border-radius:140px 140px 20px 20px;background:linear-gradient(180deg,#2a4fa8,#c8262e 55%,#2a4fa8)" role="img" aria-label="Illustrated superhero mascot in a blue and red suit with cape"></div>
<h1 class="abs display hero-title">The Coastal Breeze<br>Cooling Company</h1>
<a class="btn" style="left:100px;top:438px;width:218px;height:40px">Schedule a Service »</a>

<!-- schedule -->
<section class="abs schedule">
  <h2 class="abs display">Schedule a Service Now</h2>
  <div class="field" style="left:100px;width:168px">Name*</div>
  <div class="field" style="left:278px;width:168px">Phone*</div>
  <div class="field" style="left:456px;width:236px">Message*</div>
  <a class="btn" style="left:706px;top:93px;width:120px;height:36px">Submit</a>
</section>
<div class="fill van" style="left:845px;top:742px;width:355px;height:170px;border-radius:40px 20px 30px 30px" role="img" aria-label="Company service van with red and navy livery"></div>

<!-- about -->
<div class="abs about-frame"></div>
<div class="fill" style="left:100px;top:987px;width:460px;height:440px;background:linear-gradient(135deg,#8a8f99,#c9ccd2 50%,#5b6170)" role="img" aria-label="Technicians servicing an outdoor air conditioning unit"></div>
<div class="fill" style="left:366px;top:1248px;width:236px;height:238px;border:5px solid #fff;background:linear-gradient(135deg,#6a8fc0,#d8dde6 60%,#3a4a6a)" role="img" aria-label="Two technicians inspecting a condenser"></div>
<h2 class="abs display" style="left:645px;top:1050px;font-size:36px">About <span class="accent">Us</span></h2>
<p class="abs about-p" style="top:1122px">Sed ut perspiciatis unde omnis iste natus sit voluptatem accusantium doloremque laudantium, totam rem aperiam, eaque ipsa quae ab illo inventore veritatis et quasi architecto beatae vitae da sunt explicabo. Nemo enim ipsam voluptatem quia</p>
<p class="abs about-p" style="top:1238px">At vero eos et accusamus et iusto odio dignissimos ducus qui blanditiis praesentium voluptatum deleniti atque corrupti quos dolores et quas molestias excepturi sint occaecati cupiditate non provident, similique sunt in culpa qui officia deserunt mollitia</p>
<a class="btn" style="left:648px;top:1366px;width:160px;height:42px">Learn More »</a>
<div class="call" style="left:832px;top:1366px"><div class="ico"><svg width="18" height="18" viewBox="0 0 24 24"><path fill="#fff" d="M6.6 10.8a15.1 15.1 0 006.6 6.6l2.2-2.2c.3-.3.7-.4 1-.2 1.1.4 2.3.6 3.6.6.6 0 1 .4 1 1V20c0 .6-.4 1-1 1A17 17 0 013 4c0-.6.4-1 1-1h3.5c.6 0 1 .4 1 1 0 1.3.2 2.5.6 3.6.1.3 0 .7-.2 1z"/></svg></div><div><small>Call For Services</small><strong>727-555-0142</strong></div></div>

<!-- services -->
<section class="abs services">
  <h2 class="abs display" style="top:72px;width:1200px;text-align:center;font-size:36px">Our <span class="accent line">Services</span></h2>
  <div class="card" style="left:100px">
    <div class="photo" style="background:linear-gradient(135deg,#d9d6d0,#a39a90 50%,#6f6760)" role="img" aria-label="Technician repairing an indoor AC unit"></div>
    <div class="badge"><svg width="26" height="26" viewBox="0 0 24 24" fill="none" stroke="#fff" stroke-width="2"><path d="M14 6a4 4 0 005 5L11 19l-3-3 8-8"/><path d="M5 5l6 6"/></svg></div>
    <h3>AC Repair</h3>
    <p>At vero eos et accusamus et io dignissimos ducus qui blanditiis praesium voluptatum deleniti atque corrupti</p>
    <a>LEARN MORE »</a>
  </div>
  <div class="card" style="left:441px">
    <div class="photo" style="background:linear-gradient(135deg,#b65a45,#9aa0a8 50%,#4a5468)" role="img" aria-label="Technicians installing an outdoor AC condenser"></div>
    <div class="badge"><svg width="26" height="26" viewBox="0 0 24 24" fill="none" stroke="#fff" stroke-width="2"><rect x="4" y="6" width="16" height="12" rx="2"/><path d="M8 12h8"/></svg></div>
    <h3>AC Installation</h3>
    <p>At vero eos et accusamus et io dignissimos ducus qui blanditiis praesium voluptatum deleniti atque corrupti</p>
    <a>LEARN MORE »</a>
  </div>
  <div class="card" style="left:782px">
    <div class="photo" style="background:linear-gradient(135deg,#9bb0c8,#d7dce2 45%,#e0772f 70%,#3c4a66)" role="img" aria-label="Technician performing HVAC maintenance on condenser units"></div>
    <div class="badge"><svg width="26" height="26" viewBox="0 0 24 24" fill="none" stroke="#fff" stroke-width="2"><rect x="4" y="4" width="16" height="16" rx="2"/><circle cx="12" cy="12" r="4"/></svg></div>
    <h3>HVAC Maintenance</h3>
    <p>At vero eos et accusamus et io dignissimos ducus qui blanditiis praesium voluptatum deleniti atque corrupti</p>
    <a>LEARN MORE »</a>
  </div>
</section>

<!-- emergency -->
<svg class="abs" style="left:556px;top:2208px" width="644" height="538" role="img" aria-label="Technician working on a large outdoor condenser unit among plants">
  <defs><linearGradient id="emg" x1="0" y1="0" x2="1" y2="1"><stop offset="0" stop-color="#5f7a4a"/><stop offset=".5" stop-color="#3a4656"/><stop offset="1" stop-color="#232a36"/></linearGradient></defs>
  <polygon points="34,0 644,0 644,538 0,538" fill="url(#emg)"/>
</svg>
<h2 class="abs display" style="left:100px;top:2268px;font-size:35px">Emergency<br><span class="accent">Services</span></h2>
<p class="abs emergency-p">When your AC fails during a summer heat wave, you need a local HVAC contractor with a proven record of expertise. With more than 40 years of experience, our certified technicians have the technical proficiency you want when temperatures rise. Coastal Breeze AC are experts at air conditioning repair for all types of cooling systems. We offer 24-hour air conditioning service, fully stocked trucks for same day repairs, next day AC installation and free portable air conditioners for temporary use should you be without air overnight. When you partner with Coastal Breeze Cooling, you can rest assured that your AC will work well when you most need it.</p>
<a class="btn" style="left:100px;top:2642px;width:162px;height:42px">Contact Us »</a>
<div class="call" style="left:284px;top:2642px"><div class="ico"><svg width="18" height="18" viewBox="0 0 24 24"><path fill="#fff" d="M6.6 10.8a15.1 15.1 0 006.6 6.6l2.2-2.2c.3-.3.7-.4 1-.2 1.1.4 2.3.6 3.6.6.6 0 1 .4 1 1V20c0 .6-.4 1-1 1A17 17 0 013 4c0-.6.4-1 1-1h3.5c.6 0 1 .4 1 1 0 1.3.2 2.5.6 3.6.1.3 0 .7-.2 1z"/></svg></div><div><small>Call For Services</small><strong>727-555-0142</strong></div></div>

<!-- why choose us -->
<section class="abs why">
  <h2 class="abs display" style="top:60px;width:1200px;text-align:center;font-size:36px">Why Choose <span class="accent">Us</span></h2>
  <div class="fill" style="left:412px;top:146px;width:376px;height:376px;border-radius:50%;background:radial-gradient(circle at 50% 40%,#2f55a8,var(--navy) 60%,var(--navy-dark));box-shadow:0 0 0 6px #fff,0 0 0 8px #dfe5f0" role="img" aria-label="Superhero mascot standing with hand raised inside a navy circle"></div>
  <div class="feat left" style="left:120px;top:233px;width:245px"><span>On Time<br>Every Time</span><i class="dot"><svg width="28" height="28" viewBox="0 0 24 24" fill="none" stroke="#fff" stroke-width="2"><circle cx="12" cy="12" r="8"/><path d="M12 8v4l3 2"/></svg></i></div>
  <div class="feat left" style="left:120px;top:328px;width:245px"><span>Fixed Price<br>Repairs</span><i class="dot"><svg width="28" height="28" viewBox="0 0 24 24" fill="none" stroke="#fff" stroke-width="2"><circle cx="12" cy="12" r="3"/><circle cx="12" cy="12" r="8" stroke-dasharray="3 2"/></svg></i></div>
  <div class="feat left" style="left:120px;top:423px;width:245px"><span>Respect for<br>Your Home</span><i class="dot"><svg width="28" height="28" viewBox="0 0 24 24" fill="none" stroke="#fff" stroke-width="2"><path d="M4 11l8-7 8 7v9H4z"/><path d="M10 20v-5h4v5"/></svg></i></div>
  <div class="feat" style="left:781px;top:233px"><i class="dot"><svg width="28" height="28" viewBox="0 0 24 24" fill="none" stroke="#fff" stroke-width="2"><circle cx="12" cy="8" r="4"/><path d="M4 21c0-4 4-6 8-6s8 2 8 6"/></svg></i><span>Highly Trained<br>Specialist</span></div>
  <div class="feat" style="left:781px;top:328px"><i class="dot"><svg width="28" height="28" viewBox="0 0 24 24" fill="none" stroke="#fff" stroke-width="2"><path d="M7 11v9H4v-9zM7 11l4-7c2 0 3 1 2 4h6l-2 12H7"/></svg></i><span>100% Satisfaction<br>Guaranteed</span></div>
  <div class="feat" style="left:781px;top:423px"><i class="dot"><svg width="28" height="28" viewBox="0 0 24 24" fill="none" stroke="#fff" stroke-width="2"><path d="M12 3l8 3v6c0 5-4 8-8 9-4-1-8-4-8-9V6z"/><path d="M8 12l3 3 5-5"/></svg></i><span>Total Work<br>Guarantee</span></div>
</section>

<!-- testimonials -->
<section class="abs reviews">
  <svg class="abs" style="left:0;top:0" width="640" height="403"><polygon points="0,0 640,0 380,403 0,403" fill="var(--red)"/></svg>
  <h2 class="abs display" style="left:100px;top:80px;font-size:28px;color:#fff;letter-spacing:2px">What Our<br>Customer Say</h2>
  <a class="btn" style="left:100px;top:168px;width:190px;height:44px;background:#fff;color:var(--red);font-size:12.5px">View All Reviews »</a>
  <div class="review" style="left:484px"><p>“ Lorem ipsum dolor sit amet, consectetur adipiscing elit, sed do eiusmpr incididunt ut labore et dolore magniqua. Quis ipsum suspendisse ultrices gda. Risus commodo viverra maecenas lavel facilisis.</p><div class="who"><i class="av"></i><div><b>DANIEL REYES</b><span class="st">★★★★★</span></div></div></div>
  <div class="review" style="left:810px"><p>“ Lorem ipsum dolor sit amet, consectetur adipiscing elit, sed do eiusmpr incididunt ut labore et dolore magniqua. Quis ipsum suspendisse ultrices gda. Risus commodo viverra maecenas lavel facilisis.</p><div class="who"><i class="av"></i><div><b>DANIEL REYES</b><span class="st">★★★★★</span></div></div></div>
  <i class="arrow" style="left:1122px;top:155px"><svg width="12" height="12" viewBox="0 0 12 12"><path d="M4 2l4 4-4 4" stroke="#fff" stroke-width="2" fill="none"/></svg></i>
  <i class="arrow" style="left:1122px;top:197px"><svg width="12" height="12" viewBox="0 0 12 12"><path d="M8 2L4 6l4 4" stroke="#fff" stroke-width="2" fill="none"/></svg></i>
</section>
<div class="fill van" style="left:76px;top:3590px;width:310px;height:148px;border-radius:40px 20px 30px 30px" role="img" aria-label="Company service van with red and navy livery"></div>

<!-- works -->
<h2 class="abs display" style="top:3800px;width:1200px;text-align:center;font-size:36px">Our <span class="accent line">Works</span></h2>
<div class="tile" style="left:100px;top:3875px;width:277px;background:linear-gradient(135deg,#b7a68f,#e8e4dc 50%,#6d6458)" role="img" aria-label="Technicians working in a utility room"></div>
<div class="tile" style="left:396px;top:3875px;width:405px;background:linear-gradient(135deg,#6c7d6a,#c9ccc6 45%,#3e4552)" role="img" aria-label="Technicians repairing an indoor unit"></div>
<div class="tile" style="left:820px;top:3875px;width:277px;background:linear-gradient(135deg,#5a7fb0,#dfe4ea 45%,#8a9bb2)" role="img" aria-label="Outdoor mini-split condenser unit"></div>
<div class="tile" style="left:100px;top:4134px;width:405px;background:linear-gradient(135deg,#4d6a3c,#b8bcc2 50%,#6a6f78)" role="img" aria-label="Technician beside a new outdoor condenser"></div>
<div class="tile" style="left:524px;top:4134px;width:277px;background:linear-gradient(135deg,#6b8a4a,#9aa1a8 50%,#3d434c)" role="img" aria-label="Outdoor condenser unit in a garden"></div>
<div class="tile" style="left:820px;top:4134px;width:277px;background:linear-gradient(135deg,#8c6448,#c4a382 50%,#5a4232)" role="img" aria-label="Air handler installed in a closet"></div>

<!-- contact -->
<section class="abs contact" role="img" aria-label="Technician in a hard hat and safety vest working on HVAC equipment">
  <div class="fill" style="left:0;top:0;width:480px;height:522px;background:linear-gradient(160deg,#2a5fb8 0%,#c8d64a 40%,#2b3140 80%);opacity:.55"></div>
</section>
<h2 class="abs display" style="left:494px;top:4525px;font-size:36px;color:#fff">Contact Us</h2>
<div class="field" style="left:494px;top:4588px;width:292px;height:42px">First name</div>
<div class="field" style="left:808px;top:4588px;width:292px;height:42px">Last name</div>
<div class="field" style="left:494px;top:4654px;width:292px;height:42px">Email</div>
<div class="field" style="left:808px;top:4654px;width:292px;height:42px">Phone</div>
<div class="field" style="left:494px;top:4720px;width:606px;height:140px;align-items:flex-start;padding-top:12px">Message</div>
<a class="btn" style="left:496px;top:4890px;width:160px;height:40px">Submit »</a>

<!-- footer -->
<footer class="abs footer">
  <div class="brand" style="left:105px;top:84px;font-size:24px;color:#fff"><i style="width:22px;height:22px"></i><span>Coastal Breeze<br>Cooling Company</span></div>
  <i class="s" style="left:131px"></i><i class="s" style="left:183px"></i><i class="s" style="left:237px"></i><i class="s" style="left:289px"></i>
  <h4 style="left:466px">Quick Links</h4>
  <ul style="left:466px"><li>Home</li><li>About Us</li><li>Services</li><li>Hvac</li><li>Resources</li><li>Contact</li></ul>
  <h4 style="left:653px">Our Services</h4>
  <ul style="left:653px"><li>AC Repair</li><li>AC Installation</li><li>HVAC Maintenance</li><li>Duct Services</li></ul>
  <h4 style="left:866px">Contact Info</h4>
  <ul style="left:866px"><li>Tampa, Florida, United States</li><li>727-555-0142</li><li>hello@coastalbreezecooling.com</li></ul>
  <div class="rule"></div>
  <p class="copy">©Copyright 2024 The Coastal Breeze Cooling Company. All Rights Reserved.</p>
</footer>

</body>
</html>
```